I have an animal hospital. I want a poster to hang in each exam room to show a picture of a normal sized heart and then an enlarged heart of a dog that was fed a grain-free diet. I want to warn people not to feed grain-free diets. Maybe at the top of the poster, "Do you feed grain-free?" and then the x-ray comparison, then the warnings of Canine Dilated Cardiomyopathy.

```html
<!DOCTYPE html>
<html lang="en">
<head>
<meta charset="utf-8">
<title>Do You Feed Grain Free? – Canine Dilated Cardiomyopathy</title>
<link href="https://fonts.googleapis.com/css2?family=Montserrat:wght@300;400;700;800;900&family=Poppins:wght@700;800&display=swap" rel="stylesheet">
<style>
  :root {
    --ink: #1a1a1a;
    --deep: #0d0d0d;
    --red: #ee0000;
    --red-dark: #8e0a0a;
    --white: #ffffff;
    --grey: #5e5e5e;
    --grey-light: #a9a9a9;
    --yellow: #ffcc00;
    --grid: rgba(255,255,255,0.22);
  }
  * { margin: 0; padding: 0; box-sizing: border-box; }
  html, body { width: 848px; height: 1200px; overflow: hidden; background: var(--ink); }
  .poster {
    position: relative; width: 848px; height: 1200px; overflow: hidden;
    background: var(--ink);
    font-family: "Montserrat", sans-serif; color: var(--white);
  }
  .backdrop { position: absolute; inset: 0; }
  .headline-outline {
    position: absolute; left: 68px; top: 96px;
    font-family: "Montserrat", sans-serif; font-weight: 400; font-size: 86px;
    letter-spacing: 4px; line-height: 1;
    color: transparent; -webkit-text-stroke: 2px var(--white);
    white-space: nowrap;
  }
  .headline-solid {
    position: absolute; left: 62px; top: 172px;
    font-family: "Montserrat", sans-serif; font-weight: 900; font-size: 88px;
    letter-spacing: -5px; line-height: 1;
    background: linear-gradient(180deg, var(--red) 35%, var(--red-dark) 100%);
    -webkit-background-clip: text; background-clip: text; color: transparent;
    white-space: nowrap;
  }
  .heart-mark {
    position: absolute; left: 620px; top: 172px; width: 158px; height: 140px;
    background: linear-gradient(135deg, var(--red-dark), var(--red));
    border-radius: 50% 50% 45% 45% / 55% 55% 45% 45%;
  }
  .question-tag {
    position: absolute; left: 72px; top: 260px; width: 551px; height: 26px;
    background: var(--grey);
    box-shadow: 4px 4px 0 var(--grey-light);
    font-weight: 800; font-size: 14.5px; letter-spacing: 2.6px;
    line-height: 26px; padding-left: 20px; white-space: nowrap;
  }
  .xray {
    position: absolute;
    background: radial-gradient(ellipse at 50% 55%, #e8e8e8 0%, #9a9a9a 35%, #4a4a4a 70%, #1e1e1e 100%);
  }
  .xray-normal { left: 52px; top: 350px; width: 340px; height: 434px; }
  .xray-cdm { left: 426px; top: 350px; width: 363px; height: 442px; }
  .caption {
    position: absolute; top: 784px; height: 47px;
    background: linear-gradient(180deg, #3a3a3a 0%, var(--deep) 100%);
    font-weight: 800; font-size: 29px; letter-spacing: 1.5px;
    text-align: center; line-height: 47px;
  }
  .caption-normal { left: 56px; width: 341px; }
  .caption-cdm { left: 426px; width: 342px; }
  .side-label {
    position: absolute; left: 790px; top: 512px;
    writing-mode: vertical-rl; font-weight: 800; font-size: 10px; letter-spacing: 0.4px;
    line-height: 12px; white-space: nowrap;
  }
  .side-label span { display: block; }
  .side-label .solid { color: var(--white); }
  .side-label .hollow { color: transparent; -webkit-text-stroke: 0.6px var(--red); }
  .cdm-title {
    position: absolute; left: 0; width: 848px; top: 918px; text-align: center;
    font-family: "Montserrat", sans-serif; font-weight: 900; font-size: 94px;
    letter-spacing: -3px; line-height: 1;
    text-shadow: 0 0 10px rgba(120,0,0,0.6);
  }
  .cdm-full {
    position: absolute; left: 164px; top: 1006px; width: 519px; height: 31px;
    background: var(--ink);
    font-weight: 300; font-size: 22px; letter-spacing: 1px;
    text-align: center; line-height: 31px; white-space: nowrap;
  }
  .warning-copy {
    position: absolute; left: 60px; width: 728px; top: 1046px;
    font-family: "Poppins", sans-serif; font-weight: 700; font-size: 19px;
    letter-spacing: 0.6px; line-height: 26px; text-align: center;
  }
</style>
</head>
<body>
<main class="poster">
  <svg class="backdrop" width="848" height="1200" viewBox="0 0 848 1200" aria-hidden="true">
    <defs>
      <pattern id="grid" width="35" height="35" patternUnits="userSpaceOnUse" x="111" y="293">
        <path d="M35 0H0V35" fill="none" stroke="var(--grid)" stroke-width="0.8"/>
      </pattern>
    </defs>
    <!-- torn red corner -->
    <path d="M0 0H205L175 18 140 40 110 55 80 70 60 95 50 115 30 125 0 150Z" fill="var(--red)"/>
    <path d="M0 150 30 125 50 115 58 100 40 118 0 138Z" fill="var(--red-dark)"/>
    <!-- frame lines -->
    <path d="M30 495V150Q30 27 150 27H700Q818 27 818 145V495" fill="none" stroke="var(--white)" stroke-width="1.2" opacity="0.85"/>
    <rect x="816" y="470" width="3" height="25" fill="var(--white)"/>
    <rect x="28" y="733" width="4" height="265" fill="var(--grey-light)"/>
    <rect x="817" y="733" width="4" height="270" fill="var(--grey-light)"/>
    <!-- grids -->
    <rect x="111" y="293" width="633" height="491" fill="url(#grid)"/>
    <rect x="111" y="823" width="633" height="175" fill="url(#grid)"/>
    <!-- red wave -->
    <path d="M0 1000 70 985 140 905 250 885 325 868 440 900 560 870 690 895 760 950 848 1000V1200H0Z" fill="var(--red-dark)" opacity="0.8"/>
    <path d="M0 1003 75 995 145 920 260 900 325 876 430 905 560 880 680 905 755 960 848 1005V1200H0Z" fill="var(--red)"/>
  </svg>

  <h1>
    <span class="headline-outline">DO YOU FEED</span>
    <span class="headline-solid">GRAIN FREE?</span>
  </h1>
  <div class="heart-mark" role="img" aria-label="Red heart with dog head silhouette"></div>

  <h2 class="question-tag">WHAT IS A CANINE&nbsp; DILATED CARDIOMYOPATHY?</h2>

  <div class="xray xray-normal" role="img" aria-label="Chest x-ray of a dog with a normal sized heart"></div>
  <div class="xray xray-cdm" role="img" aria-label="Chest x-ray of a dog with an enlarged heart from dilated cardiomyopathy"></div>

  <svg style="position:absolute;left:413px;top:334px" width="136" height="136" viewBox="0 0 136 136" role="img" aria-label="Warning sign">
    <path d="M68 0 136 68 68 136 0 68Z" fill="var(--yellow)"/>
    <path d="M62 34H74L71 88H65Z" fill="var(--deep)"/>
    <rect x="62" y="94" width="12" height="11" fill="var(--deep)"/>
  </svg>

  <div class="caption caption-normal">NORMAL</div>
  <div class="caption caption-cdm">CANINE WITH CDM</div>

  <div class="side-label" aria-hidden="true">
    <span class="solid">CANINE DILATED CARDIOMYOPATHY</span>
    <span class="hollow">CANINE DILATED CARDIOMYOPATHY</span>
    <span class="hollow">CANINE DILATED CARDIOMYOPATHY</span>
  </div>

  <div class="cdm-title">CDM?</div>
  <div class="cdm-full">CANINE DILATED CARDIOMYOPATHY</div>
  <p class="warning-copy">Scientific studies have shown that grain-free diets can lead to dilated cardiomyopathy, which is a thinning of the heart wall that can lead to heart failure. If the problem is caught early enough, the problem can be resolved</p>
</main>
</body>
</html>
```